Store Front Signage for an Upscale Cake & Dessert Bakery

We need a design for store front windows. We are a 12 year old bakery specializing in cakes, cupcakes, cookies, pies, and other desserts. We recently moved to a high traffic location.. and we would like to boost our visual presence; we can be seen from the main road but are competing with other businesses for attention. Attached is a photo of our store front with posters but this signage will be for window film for the entire window span. (see the store front to the left of the photo to see the green and yellow as a film example)
Our logo and store sign (not like in photo, that is showing more red) are in shades of pink. The most visible part of the signage is in the upper third to upper half of the 60" panels.
The signs in the window currently say Life's Short. Eat Cake.
We now use Enjoy Life. Eat Cake.
The design should span all the windows and door -- this can be individual panels or one design that covers all panels. I have pink and greys chosen but please DO NOT let this constrain you. The inside of the bakery has grey floors and walls. white cabinetry, black granite countertops. The only thing with color is the baked goods and display cakes, pictures of cakes, the logo and menu and employee shirts.

Target Market(s)

we are located at a busy intersection --- we would like to capture the attention of people in cars as they pass by and entice them to stop in

Font styles to use
Serif
Sans Serif

Colors
d3d3d3
757575
ffffff
e24197
e667a6
eea4c8
f9d9e8

Requirements
Must have
• I would like the design to be easily discernible at the road way that is about 75 feet from store front. If you look at the photos I provide, note that the font size that is easily readable from the road are the ones in the top panes (although the shadow from the building makes them difficult to see -- the best visibility is the top 1/3 of the 60" panels.
Nice to have
• would like to have some non-photo graphics of a cake ( like a birthday cake), tiered cake, cupcakes, and cookies or pie for the panels --- but DO NOT let this constrain you. I need something to grab attention while cars are stopped at the nearby traffic light.
• If this design works well... I will be changing the panel on a seasonal basis
Should not have
• words that cannot be read from a distance.

```html
<!DOCTYPE html>
<html lang="en">
<head>
<meta charset="utf-8">
<title>Rosalie's Bake Shoppe – Window Film</title>
<link rel="stylesheet" href="https://fonts.googleapis.com/css2?family=Roboto+Slab:wght@300;400;600;700&display=swap">
<style>
  :root {
    --frame: #161616;
    --panel: #2a2a2a;
    --magenta: #a3125f;
    --magenta-soft: #c8609a;
    --pink-light: #f4a6c9;
    --white: #ffffff;
  }
  * { box-sizing: border-box; margin: 0; padding: 0; }
  html, body { width: 1200px; height: 638px; overflow: hidden; background: var(--frame); }
  body { font-family: "Roboto Slab", Georgia, serif; }

  .storefront {
    width: 1200px; height: 638px;
    background: var(--frame);
    padding: 10px;
    display: grid;
    grid-template-columns: 235px 245px 180px 245px 235px;
    column-gap: 10px;
  }
  .bay { display: flex; flex-direction: column; }

  .awning {
    height: 140px;
    background: linear-gradient(180deg, var(--magenta) 0%, var(--magenta-soft) 100%);
  }
  .awning-gap { height: 18px; }

  .pane {
    position: relative;
    height: 340px;
    display: flex; flex-direction: column; align-items: center; justify-content: center;
    text-align: center; color: var(--white);
  }
  .pane-texture { position: absolute; inset: 0; background: var(--panel); }
  .pane > *:not(.pane-texture) { position: relative; }

  .band-gap { height: 10px; }
  .band { height: 110px; background: var(--magenta); }
  .bay--door .band { height: 80px; }

  .offer { font-weight: 300; font-size: 21px; line-height: 1.02; }
  .dot { width: 18px; height: 18px; border-radius: 50%; background: var(--pink-light); margin: 16px 0; }
  .note { font-weight: 600; font-size: 11.5px; line-height: 1.25; letter-spacing: .3px; margin-top: 4px; }

  .brand { display: flex; align-items: center; gap: 8px; margin-bottom: 16px; }
  .brand-name { font-weight: 700; font-size: 22px; color: var(--pink-light); letter-spacing: 1px; }
  .brand-mark { width: 14px; height: 14px; border-radius: 50%; background: var(--pink-light); }
  .shop-title { font-weight: 300; font-size: 36px; line-height: 1.02; }
  .rule { width: 90px; height: 2px; background: var(--pink-light); margin-top: 18px; }

  .bay--door .brand-name { font-size: 14px; }
  .bay--door .brand { margin-bottom: 6px; }
  .bay--door .shop-title { font-size: 19px; }
  .bay--door .rule { width: 55px; margin: 8px 0 18px; }
  .hours { font-weight: 600; font-size: 9.5px; line-height: 1.4; }
</style>
</head>
<body>
<main class="storefront">

  <section class="bay">
    <div class="awning" role="img" aria-label="Scalloped magenta and white striped awning"></div>
    <div class="awning-gap"></div>
    <div class="pane">
      <div class="pane-texture" role="img" aria-label="Grey swirl damask pattern on charcoal"></div>
      <p class="offer">custom<br>cakes</p>
      <span class="dot"></span>
      <p class="offer">holiday<br>desserts</p>
      <span class="dot"></span>
      <p class="note">ORDER ONLINE<br>ROSALIESBAKES.COM</p>
    </div>
    <div class="band-gap"></div>
    <div class="band" role="img" aria-label="Magenta band with pink scroll border and swirl pattern"></div>
  </section>

  <section class="bay">
    <div class="awning" role="img" aria-label="Scalloped magenta and white striped awning"></div>
    <div class="awning-gap"></div>
    <div class="pane">
      <div class="pane-texture" role="img" aria-label="Grey swirl damask pattern on charcoal"></div>
      <div class="brand"><span class="brand-mark"></span><span class="brand-name">ROSALIE'S</span></div>
      <h1 class="shop-title">bake<br>shoppe</h1>
      <span class="rule"></span>
    </div>
    <div class="band-gap"></div>
    <div class="band" role="img" aria-label="Magenta band with pink scroll border and swirl pattern"></div>
  </section>

  <section class="bay bay--door">
    <div class="awning" role="img" aria-label="Scalloped magenta and white striped awning"></div>
    <div class="awning-gap"></div>
    <div class="pane">
      <div class="pane-texture" role="img" aria-label="Grey swirl damask pattern on charcoal"></div>
      <div class="brand"><span class="brand-name">ROSALIE'S</span></div>
      <p class="shop-title">bake<br>shoppe</p>
      <span class="rule"></span>
      <p class="hours">HOURS:<br>MONDAY-SATURDAY<br>9AM - 7PM<br>SUNDAY 11AM-5PM</p>
    </div>
    <div class="band-gap"></div>
    <div class="band" role="img" aria-label="Magenta band with pink scroll border and swirl pattern"></div>
  </section>

  <section class="bay">
    <div class="awning" role="img" aria-label="Scalloped magenta and white striped awning"></div>
    <div class="awning-gap"></div>
    <div class="pane">
      <div class="pane-texture" role="img" aria-label="Grey swirl damask pattern on charcoal"></div>
      <div class="brand"><span class="brand-mark"></span><span class="brand-name">ROSALIE'S</span></div>
      <p class="shop-title">bake<br>shoppe</p>
      <span class="rule"></span>
    </div>
    <div class="band-gap"></div>
    <div class="band" role="img" aria-label="Magenta band with pink scroll border and swirl pattern"></div>
  </section>

  <section class="bay">
    <div class="awning" role="img" aria-label="Scalloped magenta and white striped awning"></div>
    <div class="awning-gap"></div>
    <div class="pane">
      <div class="pane-texture" role="img" aria-label="Grey swirl damask pattern on charcoal"></div>
      <p class="offer">cupcakes<br>galore</p>
      <span class="dot"></span>
      <p class="offer">sweets and<br>cookies</p>
      <span class="dot"></span>
      <p class="note">NEXT DAY PICK-UP<br>DELIVERY AVAILABLE</p>
    </div>
    <div class="band-gap"></div>
    <div class="band" role="img" aria-label="Magenta band with pink scroll border and swirl pattern"></div>
  </section>

</main>
</body>
</html>
```